Truck Outfitters and Trailer Hitch Retailer Website

We are working with a hitch installer in California called Brisk Tow. They sell and install trailer hitches, bedliners for trucks, and pickup truck accessories.
Some sites to use for content/competitors:
https://www.varlomi.com/pick-up-outfitters
https://bramwells-rigs.com
https://www.thetowlodge.com
https://towlodgeinccom.quenrivsites.com
Some sites to use for inspiration:
https://www.ironmarkcouplers.com
https://quietcouplers.com
https://velmatow.com/
https://www.harborcoat.com
https://www.rugged-trailpath.com
Thank you for taking the time to consider designing a website for us. We are web developers based in Stockton, CA, USA. Most of our projects go through the same process. Understanding this process may help you win a project with us. We custom-code all of our websites in-house. We don’t have any requirements as to what tools you use for your design, but we prefer Figma files. For any design that we label as four-stars, we send it to the client for review. The client picks the final design they want us to use. Once we complete this process, we will continue to show additional clients all the four-star sites and purchase them later. Your designs will have multiple chances to sell. For better chances of success, we ask that you follow these guidelines.
IMAGES:
If you use any images or icons in the design, we ask that you have a link to the asset so we can purchase the image/icon. Most of the designs we submit do not have the customer’s images on them unless they have some great images. Be creative; show us the feeling you are trying to portray with your image choices. Use any royalty-free site you choose. We subscribe to Adobe and mainly use their images, but we can purchase images outside of Adobe.
PLEASE NOTE: we will not submit designs to clients with watermarks on the images.
FONTS:
We ask that you identify the fonts used in the design. This can be done in a message if you want. We typically use Google Fonts and Adobe Fonts.
CONTENT:
We're always open to different content and ideas. We often submit designs with stock images so the client can see our vision. We typically take pictures after the website launch to use their images with our vision. Lorem Ipsum is fine for paragraphs, but we ask that you write the headers in correct English. We want to be able to show the vision and identify the sections of the website.
INSPIRATION:
We typically add a couple of links in the brief of websites we like to help you get started in your design.
REVISIONS:
We do not often ask for revisions of the designs unless we see something in the design that may not appeal to the client. If there are slight changes that we want to make, we do that in the development process.
FEEDBACK:
We rarely give feedback on designs during the design process. We are working on many website projects and do not have the time to provide feedback. We usually respond if your request is well thought out and asks specific questions, but a note asking “feedback, please” usually goes unanswered
Number of Pages Required
1 page
Look and feel
Each slider illustrates characteristics of the customer's brand and the style your logo design should communicate.

```html
<!DOCTYPE html>
<html lang="en">
<head>
<meta charset="utf-8">
<title>Brisk Tow — Truck Outfitters &amp; Trailer Hitches</title>
<link href="https://fonts.googleapis.com/css2?family=Audiowide&family=Lato:ital,wght@0,400;0,700;0,900;1,400&family=Poppins:wght@400;600&display=swap" rel="stylesheet">
<style>
:root{
  --red:#e30613;
  --dark:#3d3d3d;
  --grey:#5b5b5b;
  --light:#f0f0f0;
  --text:#555;
  --white:#fff;
  --black:#000;
}
*{box-sizing:border-box;margin:0;padding:0}
html,body{width:1200px;height:4065px;overflow:hidden}
body{position:relative;background:var(--white);font-family:"Lato",sans-serif;color:var(--text)}
.abs{position:absolute}
.display{font-family:"Audiowide",sans-serif;text-transform:uppercase}
.red{color:var(--red)}

/* header */
.topbar{top:0;left:0;width:1200px;height:104px}
.contact-chip{top:28px;display:flex;align-items:center;gap:14px}
.chip-icon{width:46px;height:46px;border-radius:50%;background:#fff;box-shadow:0 2px 8px rgba(0,0,0,.18);display:flex;align-items:center;justify-content:center}
.chip-label{font-family:"Audiowide",sans-serif;font-size:11px;color:#444;text-transform:uppercase}
.chip-value{font-family:"Audiowide",sans-serif;font-size:14px;color:#222;text-transform:uppercase;margin-top:3px}
.nav{top:104px;left:0;width:1200px;height:78px;background:var(--grey)}
.nav a{position:absolute;top:0;height:78px;line-height:78px;font-family:"Audiowide",sans-serif;font-size:14px;color:#fff;text-decoration:none;text-transform:uppercase;text-align:center}
.nav a.active{background:var(--red)}
.brand-plate{top:0;left:448px;width:304px;height:210px;z-index:3}
.brand-name{top:116px;left:448px;width:304px;text-align:center;font-family:"Audiowide",sans-serif;font-size:30px;color:var(--dark);z-index:4;display:flex;justify-content:center;align-items:center;gap:10px}
.brand-name i{width:14px;height:14px;background:var(--red);display:inline-block}
.brand-dot{top:22px;left:568px;width:64px;height:64px;border-radius:50%;background:var(--grey);z-index:4}

/* hero */
.hero{top:182px;left:0;width:1200px;height:634px;
  background:
    radial-gradient(ellipse 260px 300px at 1120px 120px,#1d9aa6 0%,rgba(29,154,166,.6) 45%,transparent 75%),
    radial-gradient(ellipse 220px 260px at 1050px 480px,#c5301f 0%,rgba(197,48,31,.5) 45%,transparent 75%),
    radial-gradient(ellipse 320px 170px at 760px 120px,#9a948d 0%,rgba(154,148,141,.5) 50%,transparent 80%),
    radial-gradient(ellipse 200px 180px at 640px 300px,#c4a28a 0%,rgba(196,162,138,.4) 50%,transparent 80%),
    radial-gradient(ellipse 260px 240px at 640px 520px,#6f6d6a 0%,transparent 80%),
    radial-gradient(ellipse 260px 200px at 380px 80px,#6a2621 0%,rgba(106,38,33,.4) 50%,transparent 80%),
    linear-gradient(100deg,#222 0%,#2f2d2c 35%,#4a4542 60%,#3a3836 100%)}
.hero-shade{top:182px;left:0;width:1200px;height:634px;background:linear-gradient(90deg,rgba(0,0,0,.45) 0%,rgba(0,0,0,.2) 40%,transparent 60%)}
.hero-shape{top:182px;left:0}
.hero-kicker{top:292px;left:110px;font-size:20px;color:#fff}
.hero-title{top:340px;left:110px;font-size:50px;color:#fff;letter-spacing:1px;font-weight:400}
.hero-copy{top:416px;left:110px;width:410px;font-size:14.5px;font-weight:700;line-height:29px;color:#fff}
.btn{display:inline-block;font-family:"Audiowide",sans-serif;text-transform:uppercase;font-size:15px;padding:0 18px;height:46px;line-height:46px}
.btn-light{top:530px;left:110px;background:#fff;color:#222}
.dots{top:758px;left:558px;display:flex;gap:10px}
.dots span{width:13px;height:13px;border-radius:50%;background:rgba(255,255,255,.45)}
.dots span.on{background:#fff}

/* about */
.about-mark{top:900px;left:150px;width:380px;height:420px;display:flex;flex-direction:column;align-items:center;justify-content:center;gap:26px}
.about-mark .disc{width:250px;height:250px;border-radius:50%;background:var(--grey)}
.about-mark .mark-name{font-family:"Audiowide",sans-serif;font-size:44px;color:var(--dark)}
.about-body{top:888px;left:598px;width:500px}
.about-body h2{font-size:34px;color:var(--dark);font-weight:400}
.about-body p{font-size:14px;line-height:27px;margin-top:10px}
.about-body h3{font-family:"Audiowide",sans-serif;font-weight:400;font-size:17px;color:var(--red);margin-top:16px}
.btn-dark{background:var(--dark);color:#fff;margin-top:28px}

/* products */
.products-bg{top:1373px;left:0}
.section-title{left:0;width:1200px;text-align:center;font-size:44px;font-weight:400;color:var(--dark)}
.card{top:1612px;width:305px;height:376px;background:#fff;box-shadow:0 2px 10px rgba(0,0,0,.12);padding:10px}
.card.featured{border:1.5px solid var(--red)}
.card-media{width:285px;height:295px;position:relative;overflow:hidden}
.card-media .photo{position:absolute;inset:0}
.card-media svg{position:absolute;left:0;bottom:0}
.photo-hitch{background:
  radial-gradient(ellipse 90px 150px at 250px 90px,#3e5f9a 0%,rgba(62,95,154,.5) 50%,transparent 80%),
  radial-gradient(ellipse 60px 50px at 190px 140px,#d8a98c 0%,transparent 80%),
  radial-gradient(ellipse 110px 70px at 170px 200px,#b9bcbf 0%,rgba(185,188,191,.4) 55%,transparent 85%),
  radial-gradient(ellipse 70px 120px at 30px 170px,#2a2c2e 0%,transparent 85%),
  linear-gradient(180deg,#3d6227 0%,#5b7a35 45%,#7a7a6a 75%,#8a8680 100%)}
.photo-liner{background:
  radial-gradient(ellipse 160px 70px at 140px 130px,#e4e6e8 0%,rgba(228,230,232,.5) 55%,transparent 85%),
  radial-gradient(ellipse 200px 40px at 140px 80px,#b8bbbf 0%,transparent 85%),
  linear-gradient(180deg,#2f3031 0%,#5e6062 25%,#a3a6a9 50%,#8b8d90 70%,#4e5052 100%)}
.photo-truck{background:
  radial-gradient(ellipse 150px 90px at 160px 130px,#3b3c3e 0%,rgba(59,60,62,.7) 55%,transparent 85%),
  radial-gradient(ellipse 60px 40px at 170px 195px,#1c1c1d 0%,transparent 85%),
  linear-gradient(180deg,#c7cacc 0%,#a9a8a4 35%,#6c6a66 55%,#a67c55 78%,#c79a6c 100%)}
.card-label{text-align:center;font-family:"Audiowide",sans-serif;text-transform:uppercase;font-size:16px;color:#333;margin-top:22px;line-height:24px}
.card.featured .card-label{color:var(--red)}
.card-label.two{margin-top:12px}

/* features */
.features-copy{top:2264px;left:170px;width:860px;text-align:center;font-size:14px;line-height:27px}
.feature-photo{top:2358px;left:110px;width:980px;height:532px;background:
  radial-gradient(ellipse 260px 160px at 600px 270px,#c9cdd0 0%,rgba(201,205,208,.6) 50%,transparent 85%),
  radial-gradient(ellipse 160px 90px at 780px 60px,#d8b59b 0%,rgba(216,181,155,.4) 50%,transparent 85%),
  radial-gradient(ellipse 220px 120px at 780px 330px,#a4a9ad 0%,transparent 85%),
  radial-gradient(ellipse 120px 200px at 330px 430px,#1f1f1f 0%,rgba(31,31,31,.5) 50%,transparent 85%),
  radial-gradient(ellipse 220px 280px at 110px 260px,#3d2f25 0%,rgba(61,47,37,.7) 55%,transparent 90%),
  linear-gradient(180deg,#c7b89a 0%,#5e7a2e 22%,#486a26 45%,#7c7a60 70%,#9a8f78 100%)}
.hotspot{width:24px;height:24px;border-radius:50%;background:var(--red);border:2px solid #fff;color:#fff;font:700 18px/19px "Lato",sans-serif;text-align:center}

/* testimonials */
.quote-mark{top:2900px;left:100px;font-family:"Lato",sans-serif;font-weight:900;font-size:420px;line-height:.8;color:rgba(227,6,19,.13)}
.say-title{top:3088px;left:138px;font-size:42px;line-height:56px;color:var(--dark);font-weight:400}
.say-copy{top:3266px;left:155px;width:250px;font-size:13px;line-height:26px}
.review{top:3083px;left:545px;width:543px;height:272px;background:#fff;border-radius:12px;box-shadow:0 4px 24px rgba(0,0,0,.1);padding:30px 46px}
.reviewer{display:flex;gap:16px;align-items:center}
.avatar{width:68px;height:68px;border-radius:50%;background:radial-gradient(circle at 50% 55%,#d9a98a 0%,#a86f4c 55%,#5b3a26 100%)}
.reviewer-name{font-family:"Poppins",sans-serif;font-weight:600;font-size:20px;color:#222}
.reviewer-place{font-family:"Poppins",sans-serif;font-size:12px;color:#444}
.rating{display:flex;align-items:center;gap:4px;margin-top:4px}
.rating span{font-family:"Poppins",sans-serif;font-size:12px;color:#333;margin-left:12px}
.review p{font-style:italic;font-size:12px;line-height:21px;margin-top:20px;color:#666}
.arrow-btn{top:3400px;width:44px;height:44px;border-radius:50%;background:#fff;box-shadow:0 2px 8px rgba(0,0,0,.15);display:flex;align-items:center;justify-content:center}

/* footer */
.footer{top:3523px;left:0;width:1200px;height:542px;background:var(--black)}
.footer-shape{top:3523px;left:0}
.footer-dot{top:3590px;left:568px;width:64px;height:64px;border-radius:50%;background:#fff}
.footer-brand{top:3700px;left:0;width:1200px;text-align:center;font-family:"Audiowide",sans-serif;font-size:36px;color:#fff;display:flex;justify-content:center;align-items:center;gap:12px}
.footer-brand i{width:16px;height:16px;background:var(--red);display:inline-block}
.footer-nav{top:3803px;left:0;width:1200px;display:flex;justify-content:center;gap:58px}
.footer-nav a{font-family:"Audiowide",sans-serif;text-transform:uppercase;color:#fff;font-size:17px;text-decoration:none}
.footer-contact{top:3880px;display:flex;align-items:center;gap:18px;color:#fff}
.footer-contact .ic{width:48px;height:48px;border-radius:50%;background:var(--red);display:flex;align-items:center;justify-content:center}
.footer-contact .lbl{font-size:14px}
.footer-contact .val{font-family:"Audiowide",sans-serif;font-size:15px;margin-top:6px}
.copyright{top:3990px;left:0;width:1200px;text-align:center;font-family:"Audiowide",sans-serif;font-size:15px;color:#fff}
</style>
</head>
<body>

<header class="abs topbar">
  <div class="abs contact-chip" style="left:110px">
    <div class="chip-icon"><svg width="22" height="22" viewBox="0 0 24 24"><path d="M6.6 10.8a15 15 0 0 0 6.6 6.6l2.2-2.2c.3-.3.7-.4 1-.2 1.1.4 2.3.6 3.6.6.6 0 1 .4 1 1V20c0 .6-.4 1-1 1A17 17 0 0 1 3 4c0-.6.4-1 1-1h3.5c.6 0 1 .4 1 1 0 1.3.2 2.5.6 3.6.1.3 0 .7-.2 1z" fill="#555"/></svg></div>
    <div><div class="chip-label">Call us now</div><div class="chip-value">+1 555 014 2290</div></div>
  </div>
  <div class="abs contact-chip" style="left:815px">
    <div class="chip-icon"><svg width="22" height="22" viewBox="0 0 24 24"><path d="M3 6h18v12H3z" fill="#555"/><path d="M3 6l9 7 9-7" stroke="#fff" stroke-width="1.6" fill="none"/></svg></div>
    <div><div class="chip-label">Mail us</div><div class="chip-value">info@brisktow.com</div></div>
  </div>
</header>

<nav class="abs nav">
  <a class="active" href="#" style="left:87px;width:98px">Home</a>
  <a href="#" style="left:200px;width:86px">About</a>
  <a href="#" style="left:310px;width:110px">Product</a>
  <a href="#" style="left:810px;width:130px">Installers</a>
  <a href="#" style="left:965px;width:135px">Contact us</a>
</nav>

<svg class="abs brand-plate" width="304" height="210" viewBox="0 0 304 210"><polygon points="0,0 304,0 304,186 152,208 0,186" fill="#fff"/></svg>
<div class="abs brand-dot"></div>
<div class="abs brand-name">Brisk Tow<i></i></div>

<div class="abs hero" role="img" aria-label="Photo of a technician coupling a trailer hitch to a tow bar"></div>
<div class="abs hero-shade"></div>
<svg class="abs hero-shape" width="1200" height="634" viewBox="0 0 1200 634">
  <polygon points="0,452 600,628 1200,452 1200,634 0,634" fill="#fff"/>
  <polygon points="0,474 560,634 0,634" fill="var(--red)"/>
  <polygon points="1200,474 640,634 1200,634" fill="var(--red)"/>
</svg>
<div class="abs display hero-kicker">Welcome to</div>
<h1 class="abs display hero-title">Brisk Tow</h1>
<p class="abs hero-copy">We are Truck Outfitters and Trailer Hitch Retailer. We sell &amp; install trailer hitches, bedliners for trucks, and pickup truck accessories</p>
<a class="abs btn btn-light">Get started</a>
<div class="abs dots"><span></span><span></span><span class="on"></span><span></span></div>

<div class="abs about-mark"><div class="disc"></div><div class="mark-name">Brisk Tow</div></div>
<section class="abs about-body">
  <h2 class="display">About <span class="red">Brisk Tow</span></h2>
  <p>Lorem ipsum dolor sit amet, consectetur adipiscing elit, sed do eiusmod tempor incididunt ut labore et dolore magna aliqua. Ut enim ad minim citation ullamco laboris nisi ut aliquip ex ea commodo consequat.</p>
  <h3>Professional Customer Service</h3>
  <p>Duis aute irure dolor in reprehenderit in voluptate velit esse cillum dolore eu fugiat nulla pariatur. Excepteur sint occaecat cupidatat non proident, sunt in culpa qui officia deserunt mollit anim id est laborum.</p>
  <h3>Committed to Quality</h3>
  <p>Excepteur sint occaecat cupidatat non proident, sunt in culpa qui officia deserunt mollit anim id est laborum.</p>
  <a class="btn btn-dark">Read more</a>
</section>

<svg class="abs products-bg" width="1200" height="810" viewBox="0 0 1200 810">
  <polygon points="0,130 1200,0 1200,810 0,810" fill="var(--light)"/>
  <polygon points="0,54 600,58 0,130" fill="var(--red)"/>
  <polygon points="1200,668 1200,740 590,742" fill="var(--red)"/>
  <polygon points="0,810 1200,740 1200,810" fill="#fff"/>
</svg>
<h2 class="abs display section-title" style="top:1522px">Our <span class="red">Product</span></h2>

<article class="abs card" style="left:110px">
  <div class="card-media"><div class="photo photo-hitch" role="img" aria-label="Photo of a hand coupling a trailer hitch"></div>
    <svg width="285" height="70" viewBox="0 0 285 70"><polygon points="0,0 142,62 285,0 285,70 0,70" fill="#c8c8c8"/></svg></div>
  <div class="card-label">Trailer hitches</div>
</article>
<article class="abs card featured" style="left:447px">
  <div class="card-media"><div class="photo photo-liner" role="img" aria-label="Photo of an aluminium truck bed liner"></div>
    <svg width="285" height="70" viewBox="0 0 285 70"><polygon points="0,0 142,62 285,0 285,70 0,70" fill="var(--red)"/></svg></div>
  <div class="card-label">Bedliners for trucks</div>
</article>
<article class="abs card" style="left:785px">
  <div class="card-media"><div class="photo photo-truck" role="img" aria-label="Photo of a pickup truck in the desert"></div>
    <svg width="285" height="70" viewBox="0 0 285 70"><polygon points="0,0 142,62 285,0 285,70 0,70" fill="#c8c8c8"/></svg></div>
  <div class="card-label two">Pickup<br>truck accessories</div>
</article>

<h2 class="abs display section-title" style="top:2193px">Our <span class="red">Features</span></h2>
<p class="abs features-copy">Lorem ipsum dolor sit amet, consectetur adipiscing elit, sed do eiusmod tempor incididunt ut labore et dolore magna aliqua. Ut enim ad minim veniam, quis nostrud exercitation ullamco laboris nisi ut aliquip ex ea commodo consequat.</p>
<div class="abs feature-photo" role="img" aria-label="Close-up photo of a trailer coupler on a tow ball"></div>
<div class="abs hotspot" style="left:612px;top:2382px">+</div>
<div class="abs hotspot" style="left:886px;top:2372px">+</div>
<div class="abs hotspot" style="left:655px;top:2508px">+</div>
<div class="abs hotspot" style="left:467px;top:2594px">+</div>
<div class="abs hotspot" style="left:636px;top:2594px">+</div>
<div class="abs hotspot" style="left:945px;top:2586px">+</div>
<div class="abs hotspot" style="left:476px;top:2716px">+</div>
<div class="abs hotspot" style="left:811px;top:2732px">+</div>
<div class="abs hotspot" style="left:326px;top:2848px">+</div>

<div class="abs quote-mark" aria-hidden="true">&ldquo;</div>
<h2 class="abs display say-title">What our<br><span class="red">customer<br>says</span></h2>
<p class="abs say-copy">Quis autem vel eum iure reprehend erit qui in ea voluptate velit esse quam nihil molestiae.......</p>
<article class="abs review">
  <div class="reviewer">
    <div class="avatar" role="img" aria-label="Customer portrait"></div>
    <div>
      <div class="reviewer-name">Maren Hollis</div>
      <div class="reviewer-place">Dunmore, Ireland</div>
      <div class="rating">
        <svg width="138" height="22" viewBox="0 0 138 22"><g fill="#f5b800"><path id="st" d="M11 1l3 6.5 7 .8-5.2 4.8 1.4 7L11 16.6 4.8 20.1l1.4-7L1 8.3l7-.8z"/><use href="#st" x="28"/><use href="#st" x="56"/><use href="#st" x="84"/><use href="#st" x="112"/></g></svg>
        <span>Sept 06, 2024</span>
      </div>
    </div>
  </div>
  <p>Sed ut perspiciatis unde omnis iste natus error sit voluptatem accusantium doloremque laudantium, totam rem aperiam, eaque ipsa quae ab illo inventore veritatis et quasi architecto beatae vitae dicta sunt explicabo. Totam rem aperiam, eaque ipsa quae ab illo inventore .</p>
</article>
<div class="abs arrow-btn" style="left:976px"><svg width="12" height="12" viewBox="0 0 12 12"><path d="M8 1L3 6l5 5" stroke="#333" stroke-width="1.6" fill="none"/></svg></div>
<div class="abs arrow-btn" style="left:1046px"><svg width="12" height="12" viewBox="0 0 12 12"><path d="M4 1l5 5-5 5" stroke="#333" stroke-width="1.6" fill="none"/></svg></div>

<footer class="abs footer"></footer>
<svg class="abs footer-shape" width="1200" height="210" viewBox="0 0 1200 210">
  <polygon points="0,0 1200,0 1200,200 600,0 0,200" fill="var(--red)"/>
  <polygon points="0,172 600,0 1200,172 1200,185 600,14 0,185" fill="#fff"/>
  <polygon points="540,0 660,0 600,20" fill="var(--red)"/>
</svg>
<div class="abs footer-dot"></div>
<div class="abs footer-brand">Brisk Tow<i></i></div>
<nav class="abs footer-nav"><a href="#">Home</a><a href="#">About</a><a href="#">Product</a><a href="#">Installers</a><a href="#">Contact us</a></nav>
<div class="abs footer-contact" style="left:110px">
  <div class="ic"><svg width="22" height="22" viewBox="0 0 24 24"><path d="M6.6 10.8a15 15 0 0 0 6.6 6.6l2.2-2.2c.3-.3.7-.4 1-.2 1.1.4 2.3.6 3.6.6.6 0 1 .4 1 1V20c0 .6-.4 1-1 1A17 17 0 0 1 3 4c0-.6.4-1 1-1h3.5c.6 0 1 .4 1 1 0 1.3.2 2.5.6 3.6.1.3 0 .7-.2 1z" fill="#fff"/></svg></div>
  <div><div class="lbl">CALL US</div><div class="val">+1 555 014 2290</div></div>
</div>
<div class="abs footer-contact" style="left:488px">
  <div class="ic"><svg width="20" height="20" viewBox="0 0 24 24"><path d="M3 6h18v12H3z" fill="#fff"/><path d="M3 6l9 7 9-7" stroke="var(--red)" stroke-width="1.6" fill="none"/></svg></div>
  <div><div class="lbl">MAIL US</div><div class="val">info@brisktow.com</div></div>
</div>
<div class="abs footer-contact" style="left:842px">
  <div class="ic"><svg width="20" height="22" viewBox="0 0 24 26"><path d="M12 1a8 8 0 0 0-8 8c0 6 8 15 8 15s8-9 8-15a8 8 0 0 0-8-8z" fill="#fff"/><circle cx="12" cy="9" r="3" fill="var(--red)"/></svg></div>
  <div><div class="lbl">LOCATION</div><div class="val">Brisk, Tow, US</div></div>
</div>
<div class="abs copyright">Copyrights@2024.Brisk Tow.All Rights Reserved</div>

</body>
</html>
```